Bloom Path! A website showcasing who I am as a person

Bloom Path started out as idea for me to better myself as a person and work on small projects that would help me grow as a person. Now I want to build a website showcasing "Bloom Path." I want the website to showcase who I am and how I have grown both professionally and personally. I can build the raw code of the website on my own but I am not really much of a designer. I am looking for a design where I can write and post blogs, articles and share my thoughts. A little about myself and the ideas and interests that I want to share
What is Bloom Path
Who I am
Background - Professional
Brand Marketing
Email Automation
Hiking
Rock Climbing
Traveling
Exercising and Transformation
"Personal Thoughts"
Hopefully this is enough information to get people started on some designs.
Work
3 page

```html
<!DOCTYPE html>
<html lang="en">
<head>
<meta charset="utf-8">
<title>Mira Solen — Bloom Path</title>
<link rel="stylesheet" href="https://fonts.googleapis.com/css2?family=Nunito+Sans:wght@400;600;700;800&family=Open+Sans:wght@400;600;700&display=swap">
<style>
:root{
  --blue:#2f72b8;
  --blue-dark:#285f9a;
  --ink:#2b2b2b;
  --text:#555;
  --muted:#888;
  --line:#e4e4e4;
  --card-border:#dcdcdc;
  --footer:#23272e;
  --white:#fff;
  --page-bg:#f3f3f3;
}
*{box-sizing:border-box;margin:0;padding:0}
html,body{width:1200px;height:3315px;overflow:hidden}
body{background:var(--page-bg);font-family:"Open Sans",Arial,sans-serif;color:var(--text)}
.page{position:relative;width:1200px;height:3315px;overflow:hidden;background:var(--page-bg)}
.abs{position:absolute}
h1,h2,h3,h4,.brand,.nav a{font-family:"Nunito Sans",Arial,sans-serif}

/* header / hero */
.hero{left:0;top:0;width:1200px;height:518px;background:
 radial-gradient(ellipse at 18% 55%,rgba(196,118,62,.55),transparent 45%),
 radial-gradient(ellipse at 75% 70%,rgba(120,150,160,.45),transparent 55%),
 linear-gradient(180deg,#3b4650 0%,#56606a 40%,#4a4036 75%,#2e2a26 100%)}
.topbar{left:0;top:0;width:1200px;height:88px;border-bottom:1px solid rgba(255,255,255,.25);display:flex;align-items:center;padding:0 100px}
.brand{color:var(--white);font-size:25px;font-weight:700;letter-spacing:.2px}
.nav{margin-left:auto;display:flex;gap:19px;align-items:center}
.nav a{color:var(--white);font-size:14px;text-decoration:none;font-weight:600}
.hero-title{left:634px;top:158px;color:var(--white);font-size:48px;font-weight:700;font-family:"Nunito Sans",Arial,sans-serif}
.hero-text{left:636px;top:228px;width:480px;color:var(--white);font-size:18px;line-height:31px}
.hero-btn{left:636px;top:308px;width:170px;height:44px;border:2px solid rgba(255,255,255,.8);border-radius:22px;color:var(--white);font-size:13px;font-weight:700;display:flex;align-items:center;justify-content:center}
.hero-arrow{top:242px}

/* white sheet */
.sheet{left:100px;top:438px;width:1000px;height:2610px;background:var(--white)}
.profile{left:100px;top:438px;width:1000px;height:266px;background:var(--blue);border:8px solid var(--white);border-bottom:none}
.avatar{left:130px;top:462px;width:214px;height:214px;border-radius:50%;border:6px solid var(--white);background:linear-gradient(160deg,#b89a86,#6a4a3c)}
.profile-name{left:427px;top:466px;color:var(--white);font-size:31px;font-weight:600}
.profile-text{left:427px;top:524px;width:640px;color:var(--white);font-size:12px;line-height:24px}
.signature{left:427px;top:638px;width:210px;height:36px;border-radius:18px;background:linear-gradient(90deg,rgba(255,255,255,.25),rgba(255,255,255,.05))}
.sig-curve{left:360px;top:618px}

/* headings */
.section-title{font-size:28px;font-weight:600;color:var(--ink)}
.side-title{font-size:25px;font-weight:600;color:var(--ink)}

/* cards */
.card{background:var(--white);border:1px solid var(--card-border);box-shadow:0 1px 4px rgba(0,0,0,.08)}
.card-img{position:absolute;left:6px;top:6px;right:6px}
.tag{position:absolute;left:12px;top:4px;background:rgba(40,40,40,.78);color:var(--white);font-size:13px;padding:4px 14px}
.card h3{position:absolute;left:26px;right:26px;font-size:19px;line-height:30px;font-weight:700;color:var(--ink)}
.meta{position:absolute;left:26px;font-size:12.5px;color:var(--muted);display:flex;gap:10px;align-items:center}
.meta svg{vertical-align:-2px;margin-right:4px}
.excerpt{position:absolute;left:26px;right:26px;font-size:12.5px;line-height:23px;color:var(--muted)}
.btn{position:absolute;left:26px;height:32px;padding:0 18px;border:1.5px solid #bcd0e6;border-radius:16px;color:var(--blue-dark);font-size:12px;font-weight:700;display:flex;align-items:center}
.share{position:absolute;right:26px;display:flex;gap:10px}
.share span{display:flex;border:1px solid #c8ccd2;border-radius:3px;font-size:11px;overflow:hidden}
.share b{padding:3px 7px;font-weight:600;color:var(--white);background:#5d7fb0}
.share i{font-style:normal;padding:3px 6px;color:#333;background:#f5f5f5}

.big{left:120px;width:582px;height:607px}
.big .card-img{height:348px}
.small{width:278px;height:376px}
.small .card-img{height:164px}
.small h3{font-size:18px}

/* sidebar */
.newsletter{left:736px;top:829px;width:340px;height:200px;border:1px solid var(--card-border)}
.input{position:absolute;left:16px;top:18px;width:306px;height:46px;border:1px solid #ddd;font-size:11px;color:#777;padding:16px 14px}
.sign-btn{position:absolute;left:16px;top:78px;width:306px;height:44px;border:1.5px solid #bcd0e6;border-radius:22px;color:var(--blue);font-weight:700;font-size:15px;display:flex;align-items:center;justify-content:center}
.fine{position:absolute;left:16px;top:140px;width:310px;font-size:11px;line-height:20px;color:var(--muted)}

.article{left:736px;width:340px;height:80px}
.thumb{position:absolute;left:0;top:0;width:110px;height:78px;border:3px solid var(--white);box-shadow:0 0 0 1px #ddd}
.article h4{position:absolute;left:132px;top:-2px;width:210px;font-size:13.5px;line-height:22px;font-weight:700;color:var(--ink)}
.article .meta{left:132px;top:52px;font-size:11.5px}
.link{font-size:12.5px;font-weight:700;color:var(--blue-dark)}
.rule{height:1px;background:var(--line)}

.fb{left:736px;top:1717px;width:340px;height:273px;border:1px solid var(--card-border)}
.fb-cover{position:absolute;left:4px;top:4px;width:330px;height:140px;background:linear-gradient(135deg,#5f6b73,#8a7b68 60%,#4b5058)}
.fb-avatar{position:absolute;left:16px;top:16px;width:86px;height:66px;border:2px solid var(--white);background:linear-gradient(160deg,#6d86a0,#3c4c5d)}
.fb-name{position:absolute;left:112px;top:16px;color:var(--white);font-size:15px;font-weight:700;font-family:"Nunito Sans",Arial,sans-serif}
.fb-likes{position:absolute;left:112px;top:38px;color:var(--white);font-size:11.5px}
.fb-btn{position:absolute;top:108px;height:28px;padding:0 12px;background:#f6f7f9;border:1px solid #ccd0d5;font-size:12px;font-weight:700;color:#333;display:flex;align-items:center}
.fb-note{position:absolute;left:18px;top:166px;font-size:11.5px;color:#666}
.fb-friends{position:absolute;left:18px;top:196px;display:flex;gap:4px}
.fb-friends span{width:46px;height:46px;background:linear-gradient(160deg,#9a8f84,#5f6a73)}

.photos{left:736px;top:2104px;width:340px;display:grid;grid-template-columns:repeat(3,100px);gap:20px 20px;justify-content:space-between}
.photos span{height:88px;border:3px solid var(--white);box-shadow:0 0 0 1px #ddd}
.insta-btn{left:736px;top:2330px;width:216px;height:38px;border:1.5px solid #bcd0e6;border-radius:19px;color:var(--blue-dark);font-size:12px;font-weight:700;display:flex;align-items:center;justify-content:center;gap:8px}
.insta-btn i{width:14px;height:14px;background:var(--blue);border-radius:2px}

.thoughts{left:736px;top:2508px;width:340px;list-style:none}
.thoughts li{position:relative;padding-left:26px;font-size:12.5px;line-height:22px;color:var(--blue-dark);margin-bottom:20px}
.thoughts li svg{position:absolute;left:0;top:4px}

/* footer */
.footer{left:0;top:3045px;width:1200px;height:270px;background:var(--footer);border-top:4px solid var(--blue)}
.contact{display:flex;align-items:center;gap:18px;color:var(--white);font-size:13.5px;line-height:22px}
.ring{width:44px;height:44px;border-radius:50%;background:var(--white);display:flex;align-items:center;justify-content:center;flex:none}
.footer-links{left:0;width:1200px;text-align:center;color:var(--white);font-size:13.5px;line-height:28px}
.footer-rule{left:100px;top:3238px;width:1000px;height:1px;background:rgba(255,255,255,.15)}
.copy{left:100px;top:3264px;color:var(--white);font-size:12.5px}
.social{left:930px;top:3253px;display:flex;gap:12px}
.social span{width:36px;height:36px;border-radius:50%;border:1.5px solid rgba(255,255,255,.8)}
</style>
</head>
<body>
<div class="page">

  <!-- hero -->
  <div class="abs hero" role="img" aria-label="Hiker resting on a mountain ridge above a lake at dusk"></div>
  <header class="abs topbar">
    <div class="brand">Mira Solen</div>
    <nav class="nav">
      <a>What is Bloom Path</a><a>Who I am</a><a>Background - Professional</a><a>Brand Marketing</a><a>Email Automation</a><a>Hiking</a><a>More ▾</a>
      <svg width="16" height="16" viewBox="0 0 16 16"><circle cx="6.5" cy="6.5" r="5" fill="none" stroke="#fff" stroke-width="2"/><path d="M10.5 10.5L15 15" stroke="#fff" stroke-width="2.4"/></svg>
    </nav>
  </header>
  <svg class="abs hero-arrow" style="left:12px" width="18" height="30" viewBox="0 0 18 30"><path d="M14 3L4 15l10 12" fill="none" stroke="#fff" stroke-width="2.5"/></svg>
  <svg class="abs hero-arrow" style="left:1168px" width="18" height="30" viewBox="0 0 18 30"><path d="M4 3l10 12L4 27" fill="none" stroke="#fff" stroke-width="2.5"/></svg>
  <h1 class="abs hero-title">Bloom Path</h1>
  <p class="abs hero-text">Nemo enim ipsam voluptatem quia voluptas sit asper nat ur aut odit au&nbsp; quia consequuntur magni.</p>
  <div class="abs hero-btn">GET MORE INFO &gt;&gt;</div>

  <!-- sheet & profile -->
  <div class="abs sheet"></div>
  <section class="abs profile"></section>
  <div class="abs avatar" role="img" aria-label="Portrait photo of the author"></div>
  <h2 class="abs profile-name">Mira Solen</h2>
  <p class="abs profile-text">At vero eos et accusamus et iusto odio dignissimos ducimus qui blanditiis praesentium voluptatum deleniti atque corr upti quos dolores et quas molestias excepturi sint occaecati cupiditate non provident, similique sunt in culpa qui officia deserunt mollitia animi, id est laborum et dolorum fuga. Et harum quidem rerum facilis est et expedita distinctio nimos minus voluptas assumenda est, omnis dolor repellendus.</p>
  <svg class="abs sig-curve" width="60" height="50" viewBox="0 0 60 50"><path d="M4 4c4 24 22 38 50 40" fill="none" stroke="#fff" stroke-width="1.5"/><path d="M46 38l8 6-9 3" fill="none" stroke="#fff" stroke-width="1.5"/></svg>
  <div class="abs signature" role="img" aria-label="Handwritten signature of the author"></div>

  <!-- main column -->
  <h2 class="abs section-title" style="left:120px;top:762px">Latest blogs</h2>

  <article class="abs card big" style="top:830px">
    <div class="card-img" role="img" aria-label="Hand holding a phone surrounded by glowing network icons" style="background:linear-gradient(135deg,#1b3a5c,#3f7fb3 45%,#8fb7d6 70%,#2a4e72)"><span class="tag">Brand Marketing</span></div>
    <h3 style="top:370px">Nemo enim ipsam voluptatem quia voluptas sit aspnar ut odit aut fugit, sed quia consequuntur</h3>
    <div class="meta" style="top:442px"><span><svg width="12" height="12" viewBox="0 0 12 12"><rect x="1" y="2" width="10" height="9" fill="none" stroke="#2f72b8"/><path d="M1 5h10" stroke="#2f72b8"/></svg>September 1, 2014</span>|<span><svg width="11" height="12" viewBox="0 0 11 12"><circle cx="5.5" cy="3.5" r="3" fill="#2f72b8"/><path d="M0 12c0-4 11-4 11 0z" fill="#2f72b8"/></svg>Evan Hart</span>|<span>💬 0 Comments</span></div>
    <p class="excerpt" style="top:478px">At vero eos et accusamus et iusto odio dignissimos ducimus qui blanditiis praesentium volup tatum deleniti atque corrupti quos dolores et quas molestias excepturi.</p>
    <div class="btn" style="top:548px">READ MORE &gt;&gt;</div>
    <div class="share" style="top:552px"><span><b>Like</b><i>200</i></span><span><b>Share</b><i>200</i></span><span><b>+1</b><i>200</i></span></div>
  </article>

  <article class="abs card small" style="left:120px;top:1474px">
    <div class="card-img" role="img" aria-label="Laptop on a desk with city lights" style="background:linear-gradient(135deg,#3b2f3a,#b5683c 55%,#e6a45a)"><span class="tag">Email Automation</span></div>
    <h3 style="top:184px">Finibus Bonor Malorum</h3>
    <div class="meta" style="top:218px">📅 Sep1, 2014 | 👤 Evan</div>
    <p class="excerpt" style="top:250px">Nam libero tempore, cum soluta nobis est eligendi optio cumque nihil im.</p>
    <div class="btn" style="top:320px">READ MORE &gt;&gt;</div>
  </article>
  <article class="abs card small" style="left:424px;top:1474px">
    <div class="card-img" role="img" aria-label="Group of hikers on a rocky trail" style="background:linear-gradient(160deg,#a9b8c4,#8f8066 55%,#6c7350)"><span class="tag">Hiking</span></div>
    <h3 style="top:184px">Finibus Bonor Malorum</h3>
    <div class="meta" style="top:218px">📅 Sep1, 2014 | 👤 Evan</div>
    <p class="excerpt" style="top:250px">Nam libero tempore, cum soluta nobis est eligendi optio cumque nihil im.</p>
    <div class="btn" style="top:320px">READ MORE &gt;&gt;</div>
  </article>

  <article class="abs card big" style="top:1883px">
    <div class="card-img" role="img" aria-label="Climber on a rock face at sunset" style="background:linear-gradient(180deg,#e9a24a 0%,#c96d32 35%,#6b5040 70%,#3d3a36)"><span class="tag">Rock Climbing</span></div>
    <h3 style="top:370px">Nemo enim ipsam voluptatem quia voluptas sit aspnar ut odit aut fugit, sed quia consequuntur</h3>
    <div class="meta" style="top:442px">📅 September 1, 2014 | 👤 Evan Hart | 💬 0 Comments</div>
    <p class="excerpt" style="top:478px">At vero eos et accusamus et iusto odio dignissimos ducimus qui blanditiis praesentium volup tatum deleniti atque corrupti quos dolores et quas molestias excepturi.</p>
    <div class="btn" style="top:548px">READ MORE &gt;&gt;</div>
    <div class="share" style="top:552px"><span><b>Like</b><i>200</i></span><span><b>Share</b><i>200</i></span><span><b>+1</b><i>200</i></span></div>
  </article>

  <article class="abs card small" style="left:120px;top:2526px">
    <div class="card-img" role="img" aria-label="Traveler with backpack facing snowy mountains" style="background:linear-gradient(180deg,#6f9ac4,#c9d3d8 45%,#8a6a48)"><span class="tag">Traveling</span></div>
    <h3 style="top:184px">Finibus Bonor Malorum</h3>
    <div class="meta" style="top:218px">📅 Sep1, 2014 | 👤 Evan</div>
    <p class="excerpt" style="top:250px">Nam libero tempore, cum soluta nobis est eligendi optio cumque nihil im.</p>
    <div class="btn" style="top:320px">READ MORE &gt;&gt;</div>
  </article>
  <article class="abs card small" style="left:424px;top:2526px">
    <div class="card-img" role="img" aria-label="Person stretching on a beach" style="background:linear-gradient(180deg,#9fb6cc,#d7dde0 55%,#8e8a82)"><span class="tag">Exercising &amp; Transformation</span></div>
    <h3 style="top:184px">Finibus Bonor Malorum</h3>
    <div class="meta" style="top:218px">📅 Sep1, 2014 | 👤 Evan</div>
    <p class="excerpt" style="top:250px">Nam libero tempore, cum soluta nobis est eligendi optio cumque nihil im.</p>
    <div class="btn" style="top:320px">READ MORE &gt;&gt;</div>
  </article>

  <div class="abs rule" style="left:120px;top:2940px;width:582px"></div>
  <div class="abs link" style="left:120px;top:2964px">VIEW MORE BLOG &gt;&gt;</div>

  <!-- sidebar -->
  <h2 class="abs side-title" style="left:736px;top:762px">Newsletter Sign Up</h2>
  <div class="abs newsletter">
    <div class="input">ENTER YOUR EMAIL ADDRESS</div>
    <div class="sign-btn">SIGN UP</div>
    <p class="fine">By signing up, you are opting in to receive periodic communications from Path Letters</p>
  </div>

  <h2 class="abs side-title" style="left:736px;top:1100px">Recent Articles</h2>
  <div class="abs article" style="top:1160px"><div class="thumb" role="img" aria-label="Phone with charts" style="background:linear-gradient(135deg,#5a5f66,#a7adb3)"></div><h4>At vero eos et accusamus ets iusto odio dignissimo</h4><div class="meta">📅 May 26, 2016 | 👤 Evan</div></div>
  <div class="abs article" style="top:1264px"><div class="thumb" role="img" aria-label="Coastal town view" style="background:linear-gradient(135deg,#3f6f9c,#c98f5a)"></div><h4>At vero eos et accusamus ets iusto odio dignissimo</h4><div class="meta">📅 May 26, 2016 | 👤 Evan</div></div>
  <div class="abs article" style="top:1368px"><div class="thumb" role="img" aria-label="Runner on a trail" style="background:linear-gradient(135deg,#c26b3a,#7c8c9a)"></div><h4>At vero eos et accusamus ets iusto odio dignissimo</h4><div class="meta">📅 May 26, 2016 | 👤 Evan</div></div>
  <div class="abs article" style="top:1472px"><div class="thumb" role="img" aria-label="Hands on a notebook" style="background:linear-gradient(135deg,#8a5e44,#d3b69a)"></div><h4>At vero eos et accusamus ets iusto odio dignissimo</h4><div class="meta">📅 May 26, 2016 | 👤 Evan</div></div>
  <div class="abs link" style="left:736px;top:1578px">VIEW MORE &gt;&gt;</div>
  <div class="abs rule" style="left:736px;top:1629px;width:340px"></div>

  <h2 class="abs side-title" style="left:736px;top:1664px">Follow us on Circlebook</h2>
  <div class="abs fb">
    <div class="fb-cover" role="img" aria-label="Page cover photo of a hiker on a hill">
      <div class="fb-avatar" role="img" aria-label="Page profile photo"></div>
      <div class="fb-name">MIRA SOLEN</div>
      <div class="fb-likes">4,893 LIKES</div>
      <div class="fb-btn" style="left:16px">Like Page</div>
      <div class="fb-btn" style="right:16px">Sign Up</div>
    </div>
    <p class="fb-note">Be the first of your friends to like this</p>
    <div class="fb-friends" role="img" aria-label="Small profile photos of followers"><span></span><span></span><span></span><span></span><span></span><span></span></div>
  </div>
  <div class="abs rule" style="left:736px;top:2015px;width:340px"></div>

  <h2 class="abs side-title" style="left:736px;top:2050px">Recent Photos</h2>
  <div class="abs photos">
    <span role="img" aria-label="Runner on a track" style="background:linear-gradient(135deg,#4b5560,#b9c1c8)"></span>
    <span role="img" aria-label="Friends laughing together" style="background:linear-gradient(135deg,#8f4a4a,#d9a48a)"></span>
    <span role="img" aria-label="Laptop on a dark desk" style="background:linear-gradient(135deg,#2f2f2f,#777)"></span>
    <span role="img" aria-label="Group photo outdoors" style="background:linear-gradient(135deg,#c49a6c,#e8d3b4)"></span>
    <span role="img" aria-label="Green valley landscape" style="background:linear-gradient(180deg,#9ab7c9,#5d8a52)"></span>
    <span role="img" aria-label="Cafe interior" style="background:linear-gradient(135deg,#4a3a30,#b39c84)"></span>
  </div>
  <div class="abs insta-btn"><i></i>FOLLOW ON SNAPFOLIO</div>
  <div class="abs rule" style="left:736px;top:2404px;width:340px"></div>

  <h2 class="abs side-title" style="left:736px;top:2436px">Personal Thoughts</h2>
  <ul class="abs thoughts">
    <li><svg width="14" height="14" viewBox="0 0 14 14"><circle cx="7" cy="7" r="7" fill="#2f72b8"/><path d="M3.8 7.2l2.2 2.2 4.2-4.4" fill="none" stroke="#fff" stroke-width="1.6"/></svg>At vero eos et accusamus et iusto odio dignissimos mus qui blanditiis praesentium volup.</li>
    <li><svg width="14" height="14" viewBox="0 0 14 14"><circle cx="7" cy="7" r="7" fill="#2f72b8"/><path d="M3.8 7.2l2.2 2.2 4.2-4.4" fill="none" stroke="#fff" stroke-width="1.6"/></svg>Tatum deleniti atque corrupti quos dolores et quas lestias excepturi sint occaecati cupiditate.</li>
    <li><svg width="14" height="14" viewBox="0 0 14 14"><circle cx="7" cy="7" r="7" fill="#2f72b8"/><path d="M3.8 7.2l2.2 2.2 4.2-4.4" fill="none" stroke="#fff" stroke-width="1.6"/></svg>Non provident, similique sunt in culpa qui officia dese runt mollitia animi, id est laborum et dolorum fuga.</li>
    <li><svg width="14" height="14" viewBox="0 0 14 14"><circle cx="7" cy="7" r="7" fill="#2f72b8"/><path d="M3.8 7.2l2.2 2.2 4.2-4.4" fill="none" stroke="#fff" stroke-width="1.6"/></svg>Et harum quidem rerum facilis est et expedita.</li>
    <li><svg width="14" height="14" viewBox="0 0 14 14"><circle cx="7" cy="7" r="7" fill="#2f72b8"/><path d="M3.8 7.2l2.2 2.2 4.2-4.4" fill="none" stroke="#fff" stroke-width="1.6"/></svg>Nam libero tempore, cum soluta nobis est eligen.</li>
    <li><svg width="14" height="14" viewBox="0 0 14 14"><circle cx="7" cy="7" r="7" fill="#2f72b8"/><path d="M3.8 7.2l2.2 2.2 4.2-4.4" fill="none" stroke="#fff" stroke-width="1.6"/></svg>Id quod maxime placeat facere possimus, omnis vo tas assumenda est.</li>
  </ul>

  <!-- footer -->
  <footer class="abs footer"></footer>
  <div class="abs contact" style="left:210px;top:3082px">
    <span class="ring"><svg width="16" height="20" viewBox="0 0 16 20"><path d="M8 1a7 7 0 017 7c0 5-7 11-7 11S1 13 1 8a7 7 0 017-7z" fill="#23272e"/><circle cx="8" cy="8" r="2.5" fill="#fff"/></svg></span>
    <span>215 Linden Street, 4th Floor<br>Portland, OR 97205</span>
  </div>
  <div class="abs contact" style="left:526px;top:3082px">
    <span class="ring"><svg width="18" height="18" viewBox="0 0 18 18"><path d="M4 1l3 4-2 2c1 3 3 5 6 6l2-2 4 3-2 3C8 17 1 10 1 3z" fill="#23272e"/></svg></span>
    <span style="line-height:44px">+1 555 014 2290</span>
  </div>
  <div class="abs contact" style="left:750px;top:3082px">
    <span class="ring"><svg width="20" height="14" viewBox="0 0 20 14"><rect x="0" y="0" width="20" height="14" rx="1" fill="#23272e"/><path d="M1 1l9 7 9-7" fill="none" stroke="#fff" stroke-width="1.4"/></svg></span>
    <span style="line-height:44px">hello@mirasolen.com</span>
  </div>
  <div class="abs footer-links" style="top:3158px">What is Bloom Path &nbsp;|&nbsp; Who I am &nbsp;|&nbsp; Background - Professional &nbsp;|&nbsp; Brand Marketing &nbsp;|&nbsp; Email Automation &nbsp;|&nbsp; Hiking &nbsp;|&nbsp; Rock Climbing &nbsp;|<br>Traveling &nbsp;|&nbsp; Exercising and Transformation &nbsp;|&nbsp; "Personal Thoughts"</div>
  <div class="abs footer-rule"></div>
  <div class="abs copy">Copyrights © 2017, Mira Solen. All rights reserved.</div>
  <div class="abs social"><span></span><span></span><span></span><span></span></div>

</div>
</body>
</html>
```